Agriculture farming Hemp and CBD

The logo is in works with your company now, should be ready in a few days. We have our Domain (kestrelbrookhollow.com) We would like to see incorporated seed to growth, but not necessary. we would like to nature colors and some black and green. we have our farm and will be growing and selling HEMP and CBD we are based in the state of Virginia. Would like to incorporate the words pause, play, rewind if possible but not necessary.

Target Market(s)

20 years old to elderly

Coding

Coded - Design and coding required

Number of Pages Required

3 page

Font styles to use
Serif

Requirements
Must have
• I'm not sure on the must haves, we are open to any ideas, we would definitely like to see Hemp and CBD included, may the life cycle of seed to plant. We must have a pop up asking if you are 20 years old before they can enter our site and to view or purchase our product. I want the design to be totally different than what i uploaded.
Nice to have
• Would like to see natural colors as well as black and green
Should not have
• I want

```html
<!DOCTYPE html>
<html lang="en">
<head>
<meta charset="utf-8">
<title>Kestrel Brook Hollow – Hemp and CBD</title>
<link href="https://fonts.googleapis.com/css2?family=Poppins:wght@400;500;600;700&family=Open+Sans:wght@400;600&display=swap" rel="stylesheet">
<style>
:root{
  --stage:#e6e6e6;
  --green:#3bb54a;
  --green-bright:#4fd14a;
  --green-dark:#1f6b27;
  --leaf:#2e7d32;
  --ink:#1d1d1d;
  --night:#141414;
  --night-2:#1e1e1e;
  --paper:#ffffff;
  --cream:#f4f1ea;
  --muted:#6f6f6f;
  --line:#2c2c2c;
}
*{box-sizing:border-box;margin:0;padding:0}
html,body{width:1200px;height:2252px;overflow:hidden}
body{background:var(--stage);font-family:"Open Sans",Arial,sans-serif;color:var(--ink);position:relative}
.page{position:absolute;top:24px;width:508px;height:2196px;background:var(--paper);overflow:hidden;box-shadow:0 2px 10px rgba(0,0,0,.12)}
.page--home{left:72px}
.page--gate{left:620px}
h1,h2,h3,h4,.brand,.btn{font-family:"Poppins",Arial,sans-serif}
.brand{font-weight:700;color:var(--green);letter-spacing:-.2px;display:inline-flex;align-items:center;gap:4px}
.brand-dot{width:7px;height:7px;border-radius:50%;background:var(--green);display:inline-block}
.btn{display:inline-block;background:var(--green);color:#fff;font-size:6px;font-weight:600;padding:4px 10px;border-radius:2px}
.btn--dark{background:var(--night)}
.ph{display:block}

/* hero */
.hero{position:relative;height:356px;background:linear-gradient(160deg,#0d2a12 0%,#1f5a23 45%,#3a7a2e 70%,#16361a 100%);color:#fff}
.hero-photo{position:absolute;inset:0}
.topbar{position:absolute;top:0;left:0;right:0;height:10px;background:rgba(0,0,0,.55);font-size:4px;color:#cfe;padding:2px 24px;display:flex;justify-content:space-between}
.nav{position:absolute;top:14px;left:24px;right:24px;display:flex;align-items:center;justify-content:space-between}
.nav .brand{font-size:11px;color:#fff}
.nav .brand-dot{background:var(--green-bright)}
.nav ul{list-style:none;display:flex;gap:12px;font-family:"Poppins",sans-serif;font-size:5px;font-weight:500;color:#fff}
.hero h1{position:absolute;top:150px;width:100%;text-align:center;font-size:24px;font-weight:600;color:#fff}
.hero .btn{position:absolute;top:186px;left:50%;transform:translateX(-50%)}
.hero-wave{position:absolute;bottom:-1px;left:0;width:100%;height:40px}

/* welcome */
.welcome{height:300px;text-align:center;padding-top:16px}
.welcome h3{font-size:11px;font-weight:600}
.welcome .brand{font-size:20px;color:var(--green);margin-top:2px}
.welcome p.lead{font-size:5px;line-height:1.6;color:var(--muted);width:400px;margin:14px auto 0}
.features{display:flex;justify-content:center;gap:64px;margin-top:20px}
.feature{width:96px}
.feature-icon{width:34px;height:34px;border-radius:50%;background:var(--green);margin:0 auto 8px;display:flex;align-items:center;justify-content:center}
.feature h4{font-size:6px;font-weight:600}
.feature p{font-size:4.5px;color:var(--muted);line-height:1.5;margin-top:3px}

/* products */
.products{height:292px;background:linear-gradient(180deg,var(--green-bright) 0%,var(--green) 60%,#2f9c3a 100%);text-align:center;padding-top:22px}
.products h2{color:#fff;font-size:13px;font-weight:600}
.product-row{display:flex;justify-content:center;gap:8px;margin-top:22px}
.product{width:100px;background:#fff;padding:4px 4px 8px}
.product-photo{height:84px}
.product h4{font-size:5px;font-weight:600;margin:6px 0 2px}
.product p{font-size:4px;color:var(--muted);margin-bottom:6px}

/* agriculture */
.agri{height:228px;background:#f7f7f5;display:flex;align-items:center;padding:0 40px;gap:24px}
.agri-copy{width:190px}
.agri h2{font-size:11px;font-weight:600;line-height:1.3}
.agri p{font-size:4.6px;color:var(--muted);line-height:1.6;margin:8px 0 10px}
.agri-photo{width:210px;height:132px}

/* benefits */
.benefits{height:300px;text-align:center;padding-top:22px}
.eyebrow{font-family:"Poppins",sans-serif;font-size:4.5px;color:var(--green);font-weight:600;letter-spacing:.6px}
.benefits h2{font-size:12px;font-weight:600;margin-top:3px}
.benefits-body{display:flex;align-items:center;justify-content:center;gap:24px;margin-top:16px}
.benefit-leaf{width:150px;height:170px}
.benefit-grid{display:grid;grid-template-columns:120px 120px;gap:18px 14px;text-align:left}
.benefit{display:flex;gap:6px}
.benefit-icon{flex:0 0 18px;height:18px;border-radius:50%;background:var(--green);display:flex;align-items:center;justify-content:center}
.benefit h4{font-size:5.5px;font-weight:600}
.benefit p{font-size:4.3px;color:var(--muted);line-height:1.5;margin-top:2px}

/* news */
.news{height:300px;background:var(--night);text-align:center;padding-top:22px;color:#fff}
.news h2{font-size:12px;font-weight:600}
.news-grid{display:grid;grid-template-columns:200px 200px;gap:10px 14px;justify-content:center;margin-top:18px;text-align:left}
.news-item{display:flex;gap:8px}
.news-photo{flex:0 0 96px;height:96px}
.news-item h4{font-size:5.5px;font-weight:600;line-height:1.4}
.news-item p{font-size:4.3px;color:#aaa;line-height:1.5;margin:4px 0 6px}

/* newsletter */
.newsletter{position:relative;height:152px;background:var(--cream);text-align:center;padding-top:38px}
.newsletter-leaf{position:absolute;top:0;height:152px;width:110px}
.newsletter-leaf--l{left:0}
.newsletter-leaf--r{right:0}
.newsletter h2{position:relative;font-size:12px;font-weight:600}
.subscribe{position:relative;display:flex;justify-content:center;margin-top:14px}
.subscribe span{width:180px;height:16px;background:#fff;border:1px solid #ddd;font-size:5px;color:#999;text-align:left;padding:4px 6px}
.subscribe .btn{border-radius:0;padding:5px 10px}

/* footer */
.footer{height:268px;background:var(--night-2);color:#ccc;padding:30px 40px 0;position:relative}
.footer-cols{display:flex;gap:22px}
.footer-about{width:150px}
.footer .brand{font-size:13px}
.footer p{font-size:4.5px;line-height:1.7;color:#aaa}
.footer-about p{margin:8px 0 10px}
.footer-field{display:flex}
.footer-field span{width:100px;height:13px;background:#fff}
.footer-field b{width:36px;height:13px;background:var(--green)}
.footer h4{font-size:6px;font-weight:600;color:#fff;margin-bottom:8px}
.footer-col{width:86px}
.hours{font-size:4.5px;color:#aaa;line-height:1.9}
.hours div{display:flex;justify-content:space-between}
.footer-bottom{position:absolute;left:40px;right:40px;bottom:22px;border-top:1px solid var(--line);padding-top:10px;display:flex;justify-content:space-between;align-items:center}
.socials{display:flex;gap:4px}
.socials i{width:9px;height:9px;border-radius:50%;background:#555;display:block}
.payments{display:flex;gap:3px}
.payments i{width:14px;height:9px;background:#555;border-radius:1px;display:block}
.copyright{font-size:4.5px;color:#888}

/* age gate */
.gate-shade{position:absolute;inset:0;background:rgba(0,0,0,.74)}
.age-modal{position:absolute;top:118px;left:132px;width:244px;background:#fff;text-align:center;padding:14px 16px 14px}
.age-modal .brand{font-size:14px}
.age-modal h3{font-size:7px;font-weight:600;letter-spacing:.5px;margin-top:6px}
.age-modal p{font-size:5px;color:var(--muted);margin-top:4px}
.age-actions{display:flex;justify-content:center;gap:6px;margin-top:8px}
.btn--no{background:#9a9a9a}
</style>
</head>
<body>

<!-- ===== Home page ===== -->
<main class="page page--home">
  <section class="hero">
    <div class="hero-photo ph" role="img" aria-label="Hands tending young hemp plants in a green field"></div>
    <div class="topbar"><span>Call us: (540) 555-0187</span><span>hello@kestrelbrookhollow.com</span></div>
    <nav class="nav">
      <span class="brand"><span class="brand-dot"></span>kestrelbrookhollow</span>
      <ul><li>HOME</li><li>ABOUT US</li><li>PRODUCTS</li><li>BENEFITS</li><li>NEWS</li><li>CONTACT</li></ul>
    </nav>
    <h1>pause, play, rewind</h1>
    <a class="btn">Shop Now</a>
    <svg class="hero-wave" viewBox="0 0 508 40" preserveAspectRatio="none"><path d="M0 40 L0 22 Q254 -8 508 22 L508 40 Z" fill="#fff"/></svg>
  </section>

  <section class="welcome">
    <h3>Welcome to</h3>
    <div class="brand">kestrelbrookhollow</div>
    <p class="lead">We are a family farm in the heart of Virginia growing hemp from seed to harvest. Every plant is tended by hand, grown in rich soil and cared for through each stage of its life. From our fields to your home, we bring you clean, natural hemp and CBD products you can trust every single day.</p>
    <div class="features">
      <div class="feature">
        <div class="feature-icon"><svg width="16" height="16" viewBox="0 0 16 16"><path d="M8 14V6M8 8C5 8 3 6 3 3c3 0 5 2 5 5zm0 0c0-3 2-5 5-5 0 3-2 5-5 5z" fill="none" stroke="#fff" stroke-width="1.3"/></svg></div>
        <h4>Plant-based Lifestyle</h4>
        <p>Natural living rooted in the care of our own fields.</p>
      </div>
      <div class="feature">
        <div class="feature-icon"><svg width="16" height="16" viewBox="0 0 16 16"><path d="M8 15V5M8 5l-4 4M8 5l4 4M8 2v3" fill="none" stroke="#fff" stroke-width="1.3"/></svg></div>
        <h4>Hemp</h4>
        <p>Grown from seed to plant on Virginia farmland.</p>
      </div>
      <div class="feature">
        <div class="feature-icon"><svg width="16" height="16" viewBox="0 0 16 16"><path d="M8 2c3 4 4 6 4 8a4 4 0 0 1-8 0c0-2 1-4 4-8z" fill="none" stroke="#fff" stroke-width="1.3"/></svg></div>
        <h4>CBD</h4>
        <p>Pure extracts tested for quality and strength.</p>
      </div>
    </div>
  </section>

  <section class="products">
    <h2>Our Products</h2>
    <div class="product-row">
      <div class="product"><div class="product-photo ph" role="img" aria-label="Bottle of CBD oil beside hemp leaves" style="background:linear-gradient(135deg,#7a8a3a,#c7b677)"></div><h4>CBD Oil Tincture</h4><p>Full spectrum blend</p><a class="btn btn--dark">Shop Now</a></div>
      <div class="product"><div class="product-photo ph" role="img" aria-label="Bowl of hemp powder on a wooden table" style="background:linear-gradient(135deg,#5b6b2a,#b9b07a)"></div><h4>Hemp Powder</h4><p>Protein rich daily mix</p><a class="btn btn--dark">Shop Now</a></div>
      <div class="product"><div class="product-photo ph" role="img" aria-label="Glass dropper bottles with green hemp leaf" style="background:linear-gradient(135deg,#3d6b35,#a9c489)"></div><h4>Hemp Seed Oil</h4><p>Cold pressed and pure</p><a class="btn btn--dark">Shop Now</a></div>
      <div class="product"><div class="product-photo ph" role="img" aria-label="Jar of CBD balm among fresh leaves" style="background:linear-gradient(135deg,#8a7a3a,#d9cf9a)"></div><h4>CBD Balm</h4><p>Soothing topical care</p><a class="btn btn--dark">Shop Now</a></div>
    </div>
  </section>

  <section class="agri">
    <div class="agri-copy">
      <h2>Agriculture farming<br>Hemp and CBD</h2>
      <p>Our farm follows every plant through its full life cycle, from the first seed in the ground to the final harvest. We grow with patience and care so each product carries the best of the land it came from.</p>
      <a class="btn">Read More</a>
    </div>
    <div class="agri-photo ph" role="img" aria-label="Row of CBD oil bottles with hemp leaves" style="background:linear-gradient(135deg,#dfe6d4,#6e9a4c 60%,#2e5a26)"></div>
  </section>

  <section class="benefits">
    <div class="eyebrow">THE SCIENCE BEHIND US?</div>
    <h2>HEMP and CBD Benefits</h2>
    <div class="benefits-body">
      <div class="benefit-leaf ph" role="img" aria-label="Large green hemp leaf" style="background:radial-gradient(circle,#4f9a3a 0%,#2e6b26 55%,#fff 72%)"></div>
      <div class="benefit-grid">
        <div class="benefit"><div class="benefit-icon"><svg width="9" height="9" viewBox="0 0 10 10"><path d="M2 5l2 2 4-4" fill="none" stroke="#fff" stroke-width="1.3"/></svg></div><div><h4>Eases Stress</h4><p>Helps the body find calm after a long and busy day.</p></div></div>
        <div class="benefit"><div class="benefit-icon"><svg width="9" height="9" viewBox="0 0 10 10"><path d="M2 5l2 2 4-4" fill="none" stroke="#fff" stroke-width="1.3"/></svg></div><div><h4>Better Sleep</h4><p>Supports steady rest and a clear morning start.</p></div></div>
        <div class="benefit"><div class="benefit-icon"><svg width="9" height="9" viewBox="0 0 10 10"><path d="M2 5l2 2 4-4" fill="none" stroke="#fff" stroke-width="1.3"/></svg></div><div><h4>Joint Comfort</h4><p>Soothes sore muscles and joints the natural way.</p></div></div>
        <div class="benefit"><div class="benefit-icon"><svg width="9" height="9" viewBox="0 0 10 10"><path d="M2 5l2 2 4-4" fill="none" stroke="#fff" stroke-width="1.3"/></svg></div><div><h4>Healthy Skin</h4><p>Rich in fatty acids that nourish and protect skin.</p></div></div>
      </div>
    </div>
  </section>

  <section class="news">
    <h2>News And Events</h2>
    <div class="news-grid">
      <div class="news-item"><div class="news-photo ph" role="img" aria-label="Greenhouse rows of hemp plants" style="background:linear-gradient(135deg,#2d5a24,#86b36a)"></div><div><h4>Planting season opens on the farm</h4><p>Join us as the first seeds go into the spring soil.</p><a class="btn">Read More</a></div></div>
      <div class="news-item"><div class="news-photo ph" role="img" aria-label="Worker checking hemp buds in a field" style="background:linear-gradient(135deg,#3a6b2c,#a2c47a)"></div><div><h4>Harvest day tours now open</h4><p>See how we bring the crop in from the field.</p><a class="btn">Read More</a></div></div>
      <div class="news-item"><div class="news-photo ph" role="img" aria-label="Hemp field under open sky" style="background:linear-gradient(135deg,#1f4a1c,#6f9a4e)"></div><div><h4>New CBD line arrives soon</h4><p>Fresh blends made from this year's plants.</p><a class="btn">Read More</a></div></div>
      <div class="news-item"><div class="news-photo ph" role="img" aria-label="Bottles of hemp oil on a table" style="background:linear-gradient(135deg,#4b6b2a,#c2c68a)"></div><div><h4>Meet us at the market</h4><p>Find our stand at the Saturday farm market.</p><a class="btn">Read More</a></div></div>
    </div>
  </section>

  <section class="newsletter">
    <div class="newsletter-leaf newsletter-leaf--l ph" role="img" aria-label="Hemp leaves along the left edge" style="background:linear-gradient(90deg,#b9c9a6,rgba(244,241,234,0))"></div>
    <div class="newsletter-leaf newsletter-leaf--r ph" role="img" aria-label="Hemp leaves along the right edge" style="background:linear-gradient(270deg,#b9c9a6,rgba(244,241,234,0))"></div>
    <h2>Join our Newsletter</h2>
    <div class="subscribe"><span>Enter your email</span><a class="btn">Subscribe</a></div>
  </section>

  <footer class="footer">
    <div class="footer-cols">
      <div class="footer-about">
        <div class="brand"><span class="brand-dot"></span>kestrelbrookhollow</div>
        <p>A family hemp farm in Virginia growing natural products from seed to harvest.</p>
        <div class="footer-field"><span></span><b></b></div>
      </div>
      <div class="footer-col"><h4>ABOUT US</h4><p>Our Farm<br>Products<br>Benefits<br>News<br>Contact</p></div>
      <div class="footer-col"><h4>CONTACT</h4><p>1420 Meadow Run Rd<br>Virginia<br>(540) 555-0187<br>hello@kestrelbrookhollow.com</p></div>
      <div class="footer-col"><h4>HOURS</h4><div class="hours"><div><span>Mon – Fri</span><span>8am – 6pm</span></div><div><span>Saturday</span><span>9am – 4pm</span></div><div><span>Sunday</span><span>Closed</span></div></div></div>
    </div>
    <div class="footer-bottom">
      <div class="socials"><i></i><i></i><i></i><i></i></div>
      <span class="copyright">© kestrelbrookhollow.com All rights reserved.</span>
      <div class="payments"><i></i><i></i><i></i><i></i></div>
    </div>
  </footer>
</main>

<!-- ===== Home page with age gate ===== -->
<main class="page page--gate">
  <section class="hero">
    <div class="hero-photo ph" role="img" aria-label="Hands tending young hemp plants in a green field"></div>
    <div class="topbar"><span>Call us: (540) 555-0187</span><span>hello@kestrelbrookhollow.com</span></div>
    <nav class="nav">
      <span class="brand"><span class="brand-dot"></span>kestrelbrookhollow</span>
      <ul><li>HOME</li><li>ABOUT US</li><li>PRODUCTS</li><li>BENEFITS</li><li>NEWS</li><li>CONTACT</li></ul>
    </nav>
    <h1>pause, play, rewind</h1>
    <a class="btn">Shop Now</a>
    <svg class="hero-wave" viewBox="0 0 508 40" preserveAspectRatio="none"><path d="M0 40 L0 22 Q254 -8 508 22 L508 40 Z" fill="#fff"/></svg>
  </section>

  <section class="welcome">
    <h3>Welcome to</h3>
    <div class="brand">kestrelbrookhollow</div>
    <p class="lead">We are a family farm in the heart of Virginia growing hemp from seed to harvest. Every plant is tended by hand, grown in rich soil and cared for through each stage of its life. From our fields to your home, we bring you clean, natural hemp and CBD products you can trust every single day.</p>
    <div class="features">
      <div class="feature"><div class="feature-icon"></div><h4>Plant-based Lifestyle</h4><p>Natural living rooted in the care of our own fields.</p></div>
      <div class="feature"><div class="feature-icon"></div><h4>Hemp</h4><p>Grown from seed to plant on Virginia farmland.</p></div>
      <div class="feature"><div class="feature-icon"></div><h4>CBD</h4><p>Pure extracts tested for quality and strength.</p></div>
    </div>
  </section>

  <section class="products">
    <h2>Our Products</h2>
    <div class="product-row">
      <div class="product"><div class="product-photo ph" role="img" aria-label="Bottle of CBD oil beside hemp leaves" style="background:linear-gradient(135deg,#7a8a3a,#c7b677)"></div><h4>CBD Oil Tincture</h4><p>Full spectrum blend</p><a class="btn btn--dark">Shop Now</a></div>
      <div class="product"><div class="product-photo ph" role="img" aria-label="Bowl of hemp powder on a wooden table" style="background:linear-gradient(135deg,#5b6b2a,#b9b07a)"></div><h4>Hemp Powder</h4><p>Protein rich daily mix</p><a class="btn btn--dark">Shop Now</a></div>
      <div class="product"><div class="product-photo ph" role="img" aria-label="Glass dropper bottles with green hemp leaf" style="background:linear-gradient(135deg,#3d6b35,#a9c489)"></div><h4>Hemp Seed Oil</h4><p>Cold pressed and pure</p><a class="btn btn--dark">Shop Now</a></div>
      <div class="product"><div class="product-photo ph" role="img" aria-label="Jar of CBD balm among fresh leaves" style="background:linear-gradient(135deg,#8a7a3a,#d9cf9a)"></div><h4>CBD Balm</h4><p>Soothing topical care</p><a class="btn btn--dark">Shop Now</a></div>
    </div>
  </section>

  <section class="agri">
    <div class="agri-copy">
      <h2>Agriculture farming<br>Hemp and CBD</h2>
      <p>Our farm follows every plant through its full life cycle, from the first seed in the ground to the final harvest. We grow with patience and care so each product carries the best of the land it came from.</p>
      <a class="btn">Read More</a>
    </div>
    <div class="agri-photo ph" role="img" aria-label="Row of CBD oil bottles with hemp leaves" style="background:linear-gradient(135deg,#dfe6d4,#6e9a4c 60%,#2e5a26)"></div>
  </section>

  <section class="benefits">
    <div class="eyebrow">THE SCIENCE BEHIND US?</div>
    <h2>HEMP and CBD Benefits</h2>
    <div class="benefits-body">
      <div class="benefit-leaf ph" role="img" aria-label="Large green hemp leaf" style="background:radial-gradient(circle,#4f9a3a 0%,#2e6b26 55%,#fff 72%)"></div>
      <div class="benefit-grid">
        <div class="benefit"><div class="benefit-icon"></div><div><h4>Eases Stress</h4><p>Helps the body find calm after a long and busy day.</p></div></div>
        <div class="benefit"><div class="benefit-icon"></div><div><h4>Better Sleep</h4><p>Supports steady rest and a clear morning start.</p></div></div>
        <div class="benefit"><div class="benefit-icon"></div><div><h4>Joint Comfort</h4><p>Soothes sore muscles and joints the natural way.</p></div></div>
        <div class="benefit"><div class="benefit-icon"></div><div><h4>Healthy Skin</h4><p>Rich in fatty acids that nourish and protect skin.</p></div></div>
      </div>
    </div>
  </section>

  <section class="news">
    <h2>News And Events</h2>
    <div class="news-grid">
      <div class="news-item"><div class="news-photo ph" role="img" aria-label="Greenhouse rows of hemp plants" style="background:linear-gradient(135deg,#2d5a24,#86b36a)"></div><div><h4>Planting season opens on the farm</h4><p>Join us as the first seeds go into the spring soil.</p><a class="btn">Read More</a></div></div>
      <div class="news-item"><div class="news-photo ph" role="img" aria-label="Worker checking hemp buds in a field" style="background:linear-gradient(135deg,#3a6b2c,#a2c47a)"></div><div><h4>Harvest day tours now open</h4><p>See how we bring the crop in from the field.</p><a class="btn">Read More</a></div></div>
      <div class="news-item"><div class="news-photo ph" role="img" aria-label="Hemp field under open sky" style="background:linear-gradient(135deg,#1f4a1c,#6f9a4e)"></div><div><h4>New CBD line arrives soon</h4><p>Fresh blends made from this year's plants.</p><a class="btn">Read More</a></div></div>
      <div class="news-item"><div class="news-photo ph" role="img" aria-label="Bottles of hemp oil on a table" style="background:linear-gradient(135deg,#4b6b2a,#c2c68a)"></div><div><h4>Meet us at the market</h4><p>Find our stand at the Saturday farm market.</p><a class="btn">Read More</a></div></div>
    </div>
  </section>

  <section class="newsletter">
    <div class="newsletter-leaf newsletter-leaf--l ph" role="img" aria-label="Hemp leaves along the left edge" style="background:linear-gradient(90deg,#b9c9a6,rgba(244,241,234,0))"></div>
    <div class="newsletter-leaf newsletter-leaf--r ph" role="img" aria-label="Hemp leaves along the right edge" style="background:linear-gradient(270deg,#b9c9a6,rgba(244,241,234,0))"></div>
    <h2>Join our Newsletter</h2>
    <div class="subscribe"><span>Enter your email</span><a class="btn">Subscribe</a></div>
  </section>

  <footer class="footer">
    <div class="footer-cols">
      <div class="footer-about">
        <div class="brand"><span class="brand-dot"></span>kestrelbrookhollow</div>
        <p>A family hemp farm in Virginia growing natural products from seed to harvest.</p>
        <div class="footer-field"><span></span><b></b></div>
      </div>
      <div class="footer-col"><h4>ABOUT US</h4><p>Our Farm<br>Products<br>Benefits<br>News<br>Contact</p></div>
      <div class="footer-col"><h4>CONTACT</h4><p>1420 Meadow Run Rd<br>Virginia<br>(540) 555-0187<br>hello@kestrelbrookhollow.com</p></div>
      <div class="footer-col"><h4>HOURS</h4><div class="hours"><div><span>Mon – Fri</span><span>8am – 6pm</span></div><div><span>Saturday</span><span>9am – 4pm</span></div><div><span>Sunday</span><span>Closed</span></div></div></div>
    </div>
    <div class="footer-bottom">
      <div class="socials"><i></i><i></i><i></i><i></i></div>
      <span class="copyright">© kestrelbrookhollow.com All rights reserved.</span>
      <div class="payments"><i></i><i></i><i></i><i></i></div>
    </div>
  </footer>

  <div class="gate-shade"></div>
  <div class="age-modal" role="dialog" aria-label="Age verification">
    <div class="brand"><span class="brand-dot"></span>kestrelbrookhollow</div>
    <h3>AGE VERIFICATION</h3>
    <p>You must be 20 years or older to enter this site.</p>
    <div class="age-actions"><a class="btn">Yes, I am 20+</a><a class="btn btn--no">No</a></div>
  </div>
</main>

</body>
</html>
```